Business IT Services Billboard to attract local small businesses

We are Brivoqua, a premier Managed Service Provider (MSP) specializing in comprehensive IT services and VOIP phone solutions exclusively for businesses. Our goal is to create a dynamic and visually engaging billboard advertisement that not only highlights our cutting-edge IT solutions but also emphasizes our state-of-the-art VOIP phone services. This billboard should communicate our commitment to providing innovative, reliable, and holistic technology solutions.
See the attached supporting documentation.
Target Market(s)
small business
Industry/Entity Type
Information Technology
Colors
Designer to choose colors to be used in the design.
Look and feel
Each slider illustrates characteristics of the customer's brand and the style your logo design should communicate.

```html
<!DOCTYPE html>
<html lang="en">
<head>
<meta charset="utf-8">
<title>Brivoqua Billboard</title>
<link rel="stylesheet" href="https://fonts.googleapis.com/css2?family=Anton&family=Montserrat:wght@700;800&display=swap">
<style>
  :root {
    --navy: #0a1a30;
    --brand-blue: #1a78c2;
    --accent-orange: #f28c1c;
    --white: #ffffff;
    --page: #ffffff;
    --photo-light: #b9b4ab;
    --photo-mid: #7d8590;
    --photo-dark: #3b4654;
  }
  html, body {
    margin: 0;
    padding: 0;
    width: 944px;
    height: 1200px;
    overflow: hidden;
    background: var(--page);
  }
  .canvas {
    position: relative;
    width: 944px;
    height: 1200px;
  }
  .billboard {
    position: absolute;
    left: 32px;
    top: 471px;
    width: 880px;
    height: 257px;
    box-shadow: 0 4px 14px rgba(0, 0, 0, 0.25);
  }
  .billboard svg { display: block; width: 100%; height: 100%; }
  .brand-name {
    font-family: "Montserrat", sans-serif;
    font-weight: 800;
    fill: var(--brand-blue);
    letter-spacing: 4px;
  }
  .headline {
    font-family: "Anton", sans-serif;
    fill: var(--white);
  }
  .tagline {
    font-family: "Montserrat", sans-serif;
    font-weight: 700;
    fill: var(--accent-orange);
  }
  .cta-lead {
    font-family: "Montserrat", sans-serif;
    font-weight: 800;
    fill: var(--white);
  }
  .web-address {
    font-family: "Anton", sans-serif;
    fill: var(--navy);
  }
</style>
</head>
<body>
<main class="canvas">
  <section class="billboard">
    <svg viewBox="0 0 1347 393" preserveAspectRatio="none" xmlns="http://www.w3.org/2000/svg">
      <defs>
        <linearGradient id="photoTone" x1="0" y1="0" x2="1" y2="1">
          <stop offset="0" stop-color="var(--photo-light)"/>
          <stop offset="0.55" stop-color="var(--photo-mid)"/>
          <stop offset="1" stop-color="var(--photo-dark)"/>
        </linearGradient>
      </defs>

      <rect class="panel-navy" x="0" y="0" width="1347" height="393" fill="var(--navy)"/>

      <polygon class="cta-band-blue" points="0,292 360,292 400,393 0,393" fill="var(--brand-blue)"/>
      <polygon class="cta-band-white" points="360,292 953,292 1000,393 400,393" fill="var(--white)"/>

      <polygon class="chevron-stripe" points="1012,0 1040,0 928,180 1045,393 1000,393 900,180" fill="var(--brand-blue)"/>

      <g role="img" aria-label="Photo of smiling support staff wearing headsets working at computers in a bright office">
        <polygon class="team-photo" points="1040,0 1347,0 1347,393 1045,393 928,180" fill="url(#photoTone)"/>
      </g>

      <text class="brand-name" x="468" y="76" font-size="50" text-anchor="middle">BRIVOQUA</text>

      <text class="headline" x="468" y="152" font-size="56" text-anchor="middle" textLength="536" lengthAdjust="spacingAndGlyphs">SEAMLESS TECHNOLOGY</text>
      <text class="headline" x="468" y="203" font-size="56" text-anchor="middle" textLength="828" lengthAdjust="spacingAndGlyphs">SOLUTIONS FOR MODERN BUSINESSES</text>

      <text class="tagline" x="468" y="241" font-size="25" text-anchor="middle" textLength="682" lengthAdjust="spacingAndGlyphs">IT AND VOIP SOLUTIONS TAILORED FOR YOUR</text>
      <text class="tagline" x="468" y="269" font-size="25" text-anchor="middle" textLength="310" lengthAdjust="spacingAndGlyphs">BUSINESS SUCCESS.</text>

      <text class="cta-lead" x="57" y="333" font-size="28" textLength="288" lengthAdjust="spacingAndGlyphs">TRANSFORM YOUR</text>
      <text class="cta-lead" x="57" y="366" font-size="28" textLength="244" lengthAdjust="spacingAndGlyphs">TECH TODAY AT</text>

      <text class="web-address" x="418" y="369" font-size="54" textLength="532" lengthAdjust="spacingAndGlyphs">WWW.BRIVOQUA.COM</text>
    </svg>
  </section>
</main>
</body>
</html>
```